Casa Morellina Togo Menu seperated in categories

new to go menu for italian restaurant with menu descriptions and prices i like the cover first page to have all the restaurant information, the other pages should be separated in the menu categories, and if we can include a map with the location of the restaurant
Casa Morellina
42 Route 83 S
North Myrtle Beach, SC 29582
open 7 days a week 4-10
Happy hour served Daily at the Bar 4-7
www.casamorellina.com
casamorellinadine@maildrop.example

Restaurant

Sans Serif

Must have
• Prices and pictures and restaurant information

```html
<!DOCTYPE html>
<html lang="en">
<head>
<meta charset="utf-8">
<title>Casa Morellina – Antipasti</title>
<link href="https://fonts.googleapis.com/css2?family=Questrial&family=Didact+Gothic&display=swap" rel="stylesheet">
<style>
  :root {
    --tan: #cd8c5c;
    --panel: #f2f4f6;
    --green: #3a8572;
    --crimson: #b8134a;
    --white: #ffffff;
    --ink: #1a1a1a;
  }
  html, body {
    margin: 0;
    padding: 0;
    width: 849px;
    height: 1200px;
    overflow: hidden;
    background: var(--tan);
  }
  .menu-page {
    position: relative;
    width: 849px;
    height: 1200px;
    background: var(--tan);
    font-family: "Didact Gothic", "Questrial", sans-serif;
  }
  .frame {
    position: absolute;
    inset: 0;
    width: 849px;
    height: 1200px;
  }
  .section {
    position: absolute;
    left: 121px;
    top: 116px;
    width: 607px;
  }
  .section-title {
    margin: 0 0 20px;
    font-family: "Questrial", sans-serif;
    font-weight: 400;
    font-size: 20px;
    line-height: 24px;
    color: var(--green);
    -webkit-text-stroke: 0.7px var(--green);
    letter-spacing: 0.3px;
  }
  .dish {
    margin: 0 0 19.5px;
  }
  .dish-name {
    margin: 0;
    font-family: "Questrial", sans-serif;
    font-weight: 400;
    font-size: 19.5px;
    line-height: 22px;
    color: var(--crimson);
  }
  .dish-desc {
    margin: 0;
    font-size: 16.5px;
    line-height: 21px;
    color: var(--ink);
  }
  .dish-desc .line {
    display: block;
    white-space: nowrap;
  }
  .dish-desc .line.full {
    text-align: justify;
    text-align-last: justify;
  }
  .dish-price {
    margin: 0;
    font-size: 16.5px;
    line-height: 21px;
    color: var(--ink);
  }
</style>
</head>
<body>
<main class="menu-page">
  <svg class="frame" viewBox="0 0 827 1169" preserveAspectRatio="none" aria-hidden="true">
    <defs>
      <linearGradient id="border-tones" x1="0" y1="0" x2="1" y2="1">
        <stop offset="0" stop-color="#3a8572"/>
        <stop offset="0.5" stop-color="#e9e4e2"/>
        <stop offset="1" stop-color="#b8134a"/>
      </linearGradient>
      <radialGradient id="plate-tones" cx="50%" cy="45%" r="60%">
        <stop offset="0" stop-color="#9a3a1c"/>
        <stop offset="0.55" stop-color="#c9853c"/>
        <stop offset="1" stop-color="#3a1a10"/>
      </radialGradient>
    </defs>
    <rect x="57" y="48" width="713" height="1072" rx="18" fill="url(#border-tones)" role="img" aria-label="Decorative border in green, white and red"/>
    <rect x="104" y="95" width="619" height="987" fill="#f2f4f6"/>
    <ellipse cx="413" cy="945" rx="172" ry="105" fill="#b8134a"/>
    <ellipse cx="392" cy="955" rx="148" ry="94" fill="url(#plate-tones)" role="img" aria-label="Photo of spaghetti with meatballs in tomato sauce"/>
  </svg>

  <section class="section">
    <h1 class="section-title">ANTIPASTI</h1>

    <article class="dish">
      <h2 class="dish-name">Mozzarella Completa</h2>
      <p class="dish-desc"><span class="line full">Mozzarella, Roasted Red Peppers, Ricotta Cheese, Fresh Tomatoes, Pro-</span><span class="line">sciutto Di Parma, Drizzled with Evoo &amp; Aged Balsamic</span></p>
      <p class="dish-price">9.95</p>
    </article>

    <article class="dish">
      <h2 class="dish-name">Fried Calamari</h2>
      <p class="dish-desc"><span class="line full">Calamari Lightly Breaded, Fried to Perfection, Served with Homemade</span><span class="line">Spicy Marinara Sauce</span></p>
      <p class="dish-price">8.95</p>
    </article>

    <article class="dish">
      <h2 class="dish-name">Escargot</h2>
      <p class="dish-desc"><span class="line full">Escargot in a Creamy Gorgonzola Cheese Sauce, Garlic, Sundried Toma-</span><span class="line">toes, Baked to Perfection</span></p>
      <p class="dish-price">9.95</p>
    </article>

    <article class="dish">
      <h2 class="dish-name">Zuppa Di Cozze</h2>
      <p class="dish-desc"><span class="line">Fresh PEI Mussels in a choice of Marinara or Lemon Fusion Sauce</span></p>
      <p class="dish-price">8.95</p>
    </article>

    <article class="dish">
      <h2 class="dish-name">Mozzarella Caprese</h2>
      <p class="dish-desc"><span class="line full">Fresh Tomato, Homemade Mozzarella, Fresh Basil, Roasted Red Peppers,</span><span class="line">Evoo and Balsamic</span></p>
      <p class="dish-price">8.95</p>
    </article>

    <article class="dish">
      <h2 class="dish-name">Shrimp Florentine</h2>
      <p class="dish-desc"><span class="line full">Jumbo Shrimp wrapped in Prosciutto, in a Lemon Infusion Sauce, served</span><span class="line">over Spinach</span></p>
      <p class="dish-price">11.95</p>
    </article>

    <article class="dish">
      <h2 class="dish-name">Clams Oreganata</h2>
      <p class="dish-desc"><span class="line full">Fresh Little Neck Clams topped with Italian Seasoned Bred Crumbs and</span><span class="line">Baked to Perfection</span></p>
      <p class="dish-price">8.95</p>
    </article>
  </section>
</main>
</body>
</html>
```